Verodex business card

Business card for sustainable investment company called "Verodex". Verodex is an exchange platform selling carbon credits between buyers and sellers. Carbon Credits are an environmental commodity for reducing global carbon emissions.

the card should obviously have our logo and the theme should be sustainability/environment mixed with a trading platform.

Contact Information for Business Card

Logo, Name, Title, Phone, Email

Colors
0054AA
0677BA
7BADD7
CADEEF
E8F1F8
0094D4
00A9DD
6FCCEA
C7EBF8
E9F6FB
00AB8E
00BBA5
67D7C9
C6EFE9
E9F9F6
59FF00
82FF00
B8FF75
E3FFCB
F4FFEA

```html
<!DOCTYPE html>
<html lang="en">
<head>
<meta charset="UTF-8">
<title>Verodex Business Card</title>
<link href="https://fonts.googleapis.com/css2?family=Montserrat:wght@400;500;700;800&display=swap" rel="stylesheet">
<style>
  :root {
    --bg: #e4e7eb;
    --navy: #14284f;
    --ink: #1b1f2a;
    --sky: #2fc0e8;
    --aqua: #67cfe0;
    --royal: #3f6fbf;
    --white: #ffffff;
  }
  * { box-sizing: border-box; margin: 0; padding: 0; }
  html, body {
    width: 1200px; height: 900px; overflow: hidden;
    background: var(--bg);
    font-family: "Montserrat", Arial, sans-serif;
  }
  .stage { position: relative; width: 1200px; height: 900px; }
  .card {
    position: absolute; width: 620px; height: 354px;
    box-shadow: 0 12px 28px rgba(0,0,0,.22);
    overflow: hidden;
  }
  .card-front {
    left: 110px; top: 80px;
    background: linear-gradient(35deg, var(--aqua) 0%, var(--sky) 45%, var(--royal) 100%);
    display: flex; align-items: center; justify-content: center;
  }
  .front-wordmark {
    color: var(--white); font-weight: 700; font-size: 58px; letter-spacing: 4px;
  }
  .card-back { left: 470px; top: 470px; background: var(--white); }
  .back-wave { position: absolute; inset: 0; }
  .back-wordmark {
    position: absolute; left: 60px; top: 110px;
    color: var(--navy); font-weight: 700; font-size: 40px; letter-spacing: 3px;
  }
  .identity { position: absolute; right: 40px; top: 40px; text-align: right; }
  .identity-name { font-weight: 800; font-size: 21px; letter-spacing: .5px; color: var(--navy); line-height: 1.2; }
  .identity-name .surname { color: var(--sky); }
  .identity-title { font-weight: 500; font-size: 14px; color: var(--ink); margin-top: 2px; }
  .edge-tab {
    position: absolute; right: 0; top: 0; width: 16px; height: 44px;
    background: linear-gradient(180deg, var(--royal), var(--sky));
  }
  .contacts { position: absolute; left: 60px; top: 190px; list-style: none; }
  .contacts li {
    display: flex; align-items: center; gap: 10px;
    font-size: 15px; font-weight: 500; color: var(--ink); margin-bottom: 6px;
  }
  .contacts svg { width: 16px; height: 16px; flex: none; }
</style>
</head>
<body>
<main class="stage">
  <section class="card card-front" aria-label="Card front">
    <span class="front-wordmark">VERODEX</span>
  </section>

  <section class="card card-back" aria-label="Card back">
    <svg class="back-wave" viewBox="0 0 620 354" preserveAspectRatio="none" aria-hidden="true">
      <defs>
        <linearGradient id="waveFill" x1="0" y1="1" x2="1" y2="0">
          <stop offset="0" stop-color="#67cfe0"/>
          <stop offset=".5" stop-color="#2fb3e6"/>
          <stop offset="1" stop-color="#3f6fbf"/>
        </linearGradient>
      </defs>
      <path fill="#14284f" d="M0,290 C190,318 310,296 400,230 C480,172 550,150 620,140 L620,354 L0,354 Z"/>
      <path fill="#ffffff" d="M0,302 C190,330 315,308 406,240 C486,182 556,160 620,150 L620,354 L0,354 Z"/>
      <path fill="url(#waveFill)" d="M0,310 C190,338 320,316 412,248 C492,190 560,168 620,158 L620,354 L0,354 Z"/>
    </svg>

    <span class="edge-tab" aria-hidden="true"></span>
    <div class="identity">
      <p class="identity-name">DANIEL <span class="surname">HARTWELL</span></p>
      <p class="identity-title">Co-Founder</p>
    </div>

    <span class="back-wordmark">VERODEX</span>

    <ul class="contacts">
      <li>
        <svg viewBox="0 0 16 16" aria-hidden="true"><path fill="#2fb3e6" d="M2 3c0-1 1-2 2-2h8c1 0 2 1 2 2v2h-3V4H5v1H2zM3 7h10l1 7H2z"/></svg>
        555-014-2286
      </li>
      <li>
        <svg viewBox="0 0 16 16" aria-hidden="true"><rect x="1" y="3" width="14" height="10" fill="#2fb3e6"/><path d="M1 3l7 6 7-6" fill="none" stroke="#fff" stroke-width="1.4"/></svg>
        info@verodex.com
      </li>
      <li>
        <svg viewBox="0 0 16 16" aria-hidden="true"><circle cx="8" cy="8" r="7" fill="#2fb3e6"/><ellipse cx="8" cy="8" rx="3" ry="7" fill="none" stroke="#fff" stroke-width="1"/><path d="M1 8h14" stroke="#fff" stroke-width="1"/></svg>
        www.verodex.com
      </li>
    </ul>
  </section>
</main>
</body>
</html>
```